Modern business card design for professional copywriter

I'd like a business card design that I can use to have my cards printed out by quillprint.com as a squared corners business card (see artwork and design guidelines here: https://help.quillprint.com/hc/en-gb/sections/200570950-QUILL-Product-Templates)

The design should be clean and modern and reflect the colours, tone and branding on my website: https://tessavorrin.com.au

Target Market(s)

Professionals, B2B small business owners

Industry/Entity Type

Business

Contact Information for Business Card

Tessa Vorrin
m: 0468 905 327
e: tessa@tessavorrin.com.au
w: tessavorrin.com.au

Font styles to use
Sans Serif

Requirements
Must have
• Tagline: "Clear writing that helps busy owners grow"
• Brand colours: fd8000, 009984, 666666 and black
Nice to have

```html
<!DOCTYPE html>
<html lang="en">
<head>
<meta charset="utf-8">
<title>Tessa Vorrin – Business Card</title>
<link href="https://fonts.googleapis.com/css2?family=Jost:wght@400;500&display=swap" rel="stylesheet">
<style>
  :root {
    --orange: #fd8000;
    --teal: #009984;
    --grey: #666666;
    --ink: #222222;
    --card: #ffffff;
    --backdrop: #efeeea;
  }
  * { box-sizing: border-box; margin: 0; padding: 0; }
  html, body {
    width: 1200px;
    height: 929px;
    overflow: hidden;
    background: var(--backdrop);
    font-family: "Jost", Arial, sans-serif;
  }
  .canvas {
    position: relative;
    width: 1200px;
    height: 929px;
  }
  .card {
    position: absolute;
    width: 540px;
    height: 309px;
    background: var(--card);
    box-shadow: 0 6px 14px rgba(0,0,0,0.18);
  }
  .card--front { left: 110px; top: 140px; }
  .card--back  { left: 550px; top: 480px; }

  .brand {
    position: absolute;
    left: 0; right: 0;
    top: 110px;
    display: flex;
    align-items: center;
    justify-content: center;
    gap: 12px;
  }
  .brand__dot {
    width: 22px; height: 22px;
    border-radius: 50%;
    background: var(--orange);
    flex: none;
  }
  .brand__name {
    font-size: 40px;
    font-weight: 500;
    line-height: 1;
    color: var(--teal);
    letter-spacing: 0.5px;
    white-space: nowrap;
  }
  .card--back .brand { top: 78px; }

  .tagline {
    position: absolute;
    left: 0; right: 0;
    bottom: 48px;
    text-align: center;
    font-size: 14px;
    line-height: 1.2;
    color: var(--ink);
    letter-spacing: 0.3px;
    white-space: nowrap;
  }

  .details {
    position: absolute;
    left: 0; right: 0;
    top: 176px;
    display: flex;
    justify-content: center;
    align-items: center;
    gap: 22px;
  }
  .person { text-align: right; line-height: 1.15; white-space: nowrap; }
  .person__name { font-size: 19px; color: var(--teal); }
  .person__role { font-size: 19px; color: var(--ink); }
  .divider {
    width: 2px; height: 60px;
    background: var(--orange);
    flex: none;
  }
  .contact { list-style: none; font-size: 14px; color: var(--grey); line-height: 1.55; white-space: nowrap; }
  .contact li { display: flex; align-items: center; gap: 9px; }
  .contact svg { width: 12px; height: 12px; flex: none; }
</style>
</head>
<body>
<main class="canvas">

  <section class="card card--front" aria-label="Card front">
    <div class="brand">
      <span class="brand__dot"></span>
      <span class="brand__name">Tessa Vorrin</span>
    </div>
    <p class="tagline">Clear writing that helps busy owners grow</p>
  </section>

  <section class="card card--back" aria-label="Card back">
    <div class="brand">
      <span class="brand__dot"></span>
      <span class="brand__name">Tessa Vorrin</span>
    </div>
    <div class="details">
      <div class="person">
        <p class="person__name">Tessa Vorrin</p>
        <p class="person__role">Copywriter</p>
      </div>
      <span class="divider"></span>
      <ul class="contact">
        <li>
          <svg viewBox="0 0 12 12" aria-hidden="true"><rect x="3" y="0.8" width="6" height="10.4" rx="1" fill="none" stroke="#009984" stroke-width="1.2"/></svg>
          0468 905 327
        </li>
        <li>
          <svg viewBox="0 0 12 12" aria-hidden="true"><rect x="0.5" y="2.5" width="11" height="7.5" fill="#009984"/><path d="M0.5 2.5 6 7 11.5 2.5" fill="none" stroke="#fff" stroke-width="1"/></svg>
          tessa@tessavorrin.com.au
        </li>
        <li>
          <svg viewBox="0 0 12 12" aria-hidden="true"><circle cx="5" cy="5" r="3.4" fill="none" stroke="#009984" stroke-width="1.6"/><path d="M7.5 7.5 11 11" stroke="#009984" stroke-width="1.8" stroke-linecap="round"/></svg>
          tessavorrin.com.au
        </li>
      </ul>
    </div>
  </section>

</main>
</body>
</html>
```